Marwick Family Chiropractic Stationary

The letterhead and business card must have our logo.
We would like to see the logo used in different ways ( It can be expanded upon in the stationary.)
Please use the the same or similar colors.
Must be eye catching and memorable.
Must be easy to read

Reason: The doctor has been too busy to make any final decisions. He would like to give himself a little more time.

Target Market(s)

Chiropractic Healthcare

Industry/Entity Type

Business

Requirements
Must have
• Dr. Leonard Marwick D.C.
Chiropractor

555-555-0183

417 Birchfield Road, 2nd Floor
Alderbrook, ST 06091

drmarwick@marwickspine.example
www.marwickspine.example
www.facebook.com/MarwickFamilySpine
Should not have
• should not be difficult to read

```html
<!DOCTYPE html>
<html lang="en">
<head>
<meta charset="utf-8">
<title>Marwick Family Chiropractic – Business Cards</title>
<link rel="stylesheet" href="https://fonts.googleapis.com/css2?family=Montserrat:wght@600;700&family=Open+Sans:wght@400;600;700&display=swap">
<style>
  :root {
    --page: #ece6de;
    --label: #2b2522;
    --card: #ffffff;
    --ink: #2a211c;
    --green: #2b9a48;
    --olive: #b4a635;
    --leaf-light: #a2cf5f;
    --night: #0b0b0b;
    --grey-text: #a9a39c;
    --mark-soft: #eef3e6;
  }
  * { box-sizing: border-box; margin: 0; padding: 0; }
  html, body { width: 1200px; height: 788px; overflow: hidden; }
  body {
    position: relative;
    background: var(--page);
    font-family: "Open Sans", Arial, sans-serif;
    color: var(--ink);
  }
  .side-label {
    position: absolute;
    width: 525px;
    text-align: center;
    font-size: 20px;
    color: var(--label);
  }
  .card {
    position: absolute;
    width: 525px;
    height: 300px;
    border-radius: 18px;
    background: var(--card);
    overflow: hidden;
    box-shadow: 0 4px 10px rgba(0,0,0,.18);
  }
  .card--front  { left: 55px;  top: 78px; }
  .card--back-1 { left: 622px; top: 75px; }
  .card--back-2 { left: 54px;  top: 446px; }
  .card--back-3 { left: 622px; top: 446px; background: var(--night); }

  .brand-dot {
    position: absolute;
    left: 50%;
    transform: translateX(-50%);
    border-radius: 50%;
    background: var(--green);
  }
  .brand-name {
    position: absolute;
    left: 0; right: 0;
    text-align: center;
    font-family: "Montserrat", Arial, sans-serif;
    font-weight: 700;
    color: var(--green);
    line-height: 1.1;
    text-transform: uppercase;
  }
  .tagline {
    position: absolute;
    left: 0; right: 0;
    text-align: center;
    font-family: "Montserrat", Arial, sans-serif;
    font-weight: 700;
    color: var(--ink);
    text-transform: uppercase;
    letter-spacing: .02em;
  }

  /* front */
  .card--front .brand-dot { top: 18px; width: 92px; height: 92px; }
  .card--front .brand-name { top: 122px; font-size: 24px; }
  .card--front .tagline { top: 150px; font-size: 11px; }
  .name-band {
    position: absolute; left: 0; right: 0; top: 185px; height: 33px;
    background: var(--green);
    color: #fff;
    text-align: center;
    font-weight: 700;
    font-size: 14.5px;
    line-height: 33px;
  }
  .name-band .role { font-size: 12.5px; }
  .contact-band {
    position: absolute; left: 0; right: 0; top: 224px; bottom: 0;
    background: var(--olive);
    color: var(--ink);
    font-size: 12.5px;
    text-align: center;
    padding-top: 8px;
    line-height: 22px;
  }
  .contact-band b { font-weight: 700; font-style: italic; }

  /* back 1 */
  .card--back-1 .brand-dot { top: 32px; width: 110px; height: 110px; }
  .card--back-1 .brand-name { top: 166px; font-size: 33px; }
  .card--back-1 .tagline { top: 204px; font-size: 13.5px; }
  .web {
    position: absolute; left: 0; right: 0; bottom: 20px;
    text-align: center; font-size: 14.5px; color: var(--ink);
  }

  /* back 2 */
  .card--back-2 .brand-dot {
    top: 24px; width: 240px; height: 240px; background: var(--mark-soft);
  }
  .card--back-2 .brand-name { top: 88px; font-size: 62px; }
  .card--back-2 .tagline { top: 162px; font-size: 25px; }

  /* back 3 */
  .card--back-3 .brand-dot { top: 28px; width: 118px; height: 118px; background: var(--leaf-light); }
  .card--back-3 .brand-name { top: 166px; font-size: 31px; color: var(--leaf-light); }
  .card--back-3 .tagline { top: 204px; font-size: 13px; color: var(--grey-text); }
  .card--back-3 .web { color: #fff; }
</style>
</head>
<body>
  <div class="side-label" style="left:55px;top:33px;">Front</div>
  <div class="side-label" style="left:622px;top:33px;">Back - 1</div>
  <div class="side-label" style="left:54px;top:403px;">Back - 2</div>
  <div class="side-label" style="left:622px;top:403px;">Back - 3</div>

  <section class="card card--front">
    <div class="brand-dot"></div>
    <div class="brand-name">Marwick</div>
    <div class="tagline">Family Chiropractic</div>
    <div class="name-band">Dr. Leonard Marwick D.C. - <span class="role">Chiropractor</span></div>
    <div class="contact-band">
      <div><b>ph :</b> 555-555-0183 &nbsp;| &nbsp;<b>e :</b> mymarwick@marwickspine.example</div>
      <div><b>w :</b> www.marwickspine.example &nbsp;| &nbsp;<b>fb :</b> MarwickFamilySpine</div>
      <div>417 Birchfield Road, 2nd Floor, Alderbrook, ST 06091</div>
    </div>
  </section>

  <section class="card card--back-1">
    <div class="brand-dot"></div>
    <div class="brand-name">Marwick</div>
    <div class="tagline">Family Chiropractic</div>
    <div class="web">www.marwickspine.example</div>
  </section>

  <section class="card card--back-2">
    <div class="brand-dot"></div>
    <div class="brand-name">Marwick</div>
    <div class="tagline">Family Chiropractic</div>
    <div class="web">www.marwickspine.example</div>
  </section>

  <section class="card card--back-3">
    <div class="brand-dot"></div>
    <div class="brand-name">Marwick</div>
    <div class="tagline">Family Chiropractic</div>
    <div class="web">www.marwickspine.example</div>
  </section>
</body>
</html>
```